Aunt Roula's Bakery

I am about to create a luxury boutique that specializes in cake baking and cupcake
and ready for parties and special events and order delivery
the logo has already made

Boutique

Email:auntroulasbakery@mailbox-example.net
Instagram: aunt_roula_bakery
Twitter: xxxxxxx
WhatsApp: xxxxxxx

Requirements
Must have
• luxury design

```html
<!DOCTYPE html>
<html lang="en">
<head>
<meta charset="utf-8">
<title>Aunt Roula's Bakery – Business Card</title>
<link rel="stylesheet" href="https://fonts.googleapis.com/css2?family=Open+Sans:wght@400;700&display=swap">
<style>
  :root {
    --page: #ecebea;
    --card: #fbfbfb;
    --ink: #1d1d1d;
    --soft-ink: #4a4a4a;
    --rose: #d79bb0;
    --rose-deep: #c9819a;
    --band: #b9b9b7;
    --band-dark: #a3a3a1;
    --ornament: #eeeeee;
    --line: #3a3a3a;
  }
  html, body {
    margin: 0;
    width: 1200px;
    height: 1022px;
    overflow: hidden;
    background: var(--page);
    font-family: "Open Sans", Arial, sans-serif;
  }
  .card {
    position: absolute;
    left: 75px;
    top: 211px;
    width: 1050px;
    height: 600px;
    background: var(--card);
    box-shadow: 0 10px 30px rgba(0,0,0,.12);
    overflow: hidden;
  }
  .flourish {
    position: absolute;
    right: 0;
    top: 0;
    width: 460px;
    height: 230px;
    background: radial-gradient(ellipse at 60% 40%, var(--ornament), transparent 70%);
  }
  .brand {
    position: absolute;
    left: 50px;
    top: 200px;
    width: 300px;
    display: flex;
    align-items: center;
    gap: 14px;
  }
  .brand-dot {
    flex: none;
    width: 56px;
    height: 56px;
    border-radius: 50%;
    background: var(--rose);
  }
  .brand-name {
    font-size: 30px;
    line-height: 1.15;
    font-weight: 400;
    color: var(--soft-ink);
    letter-spacing: 1px;
  }
  .divider {
    position: absolute;
    left: 350px;
    right: 40px;
    top: 300px;
    height: 2px;
    background: var(--line);
  }
  .owner-name {
    position: absolute;
    right: 40px;
    top: 248px;
    font-size: 36px;
    font-weight: 700;
    color: var(--ink);
    letter-spacing: .5px;
  }
  .owner-role {
    position: absolute;
    right: 40px;
    top: 306px;
    font-size: 18px;
    color: var(--rose-deep);
    letter-spacing: 1px;
  }
  .contacts {
    position: absolute;
    left: 360px;
    top: 328px;
    margin: 0;
    padding: 0;
    list-style: none;
    font-size: 22px;
    color: var(--ink);
  }
  .contacts li {
    display: flex;
    align-items: center;
    gap: 12px;
    height: 32px;
  }
  .contact-mark {
    flex: none;
    width: 13px;
    height: 13px;
    border: 2px solid var(--rose);
    border-radius: 3px;
  }
  .base-band {
    position: absolute;
    left: 0;
    bottom: 0;
    width: 1050px;
    height: 90px;
  }
</style>
</head>
<body>
  <div class="card">
    <div class="flourish" role="img" aria-label="Faint decorative swirl ornament"></div>

    <div class="brand">
      <span class="brand-dot"></span>
      <span class="brand-name">Aunt Roula's Bakery</span>
    </div>

    <div class="owner-name">AUNT ROULA</div>
    <div class="divider"></div>
    <div class="owner-role">OWNER</div>

    <ul class="contacts">
      <li><span class="contact-mark"></span>xxxxxxx</li>
      <li><span class="contact-mark"></span>xxxxxxx</li>
      <li><span class="contact-mark"></span>aunt_roula_bakery</li>
      <li>
        <svg width="17" height="13" viewBox="0 0 17 13" aria-hidden="true">
          <rect x="1" y="1" width="15" height="11" fill="none" stroke="#d79bb0" stroke-width="2"/>
          <path d="M1 1 L8.5 7 L16 1" fill="none" stroke="#d79bb0" stroke-width="2"/>
        </svg>
        auntroulasbakery@mailbox-example.net
      </li>
    </ul>

    <svg class="base-band" viewBox="0 0 1050 90" aria-hidden="true">
      <polygon points="0,0 610,0 650,90 0,90" fill="var(--band)"/>
      <polygon points="610,0 650,90 640,90 602,8" fill="var(--band-dark)"/>
      <rect x="650" y="62" width="400" height="28" fill="var(--rose)"/>
    </svg>
  </div>
</body>
</html>
```